Harlow Creek Church Invite Card

We are a vibrant multigenerational church outside of Raleigh, NC and are wanting a 'church invite card' that we can encourage our members to carry with them so that they can invite their friends to church.

These cards should have a modern feel (see http://brightmosaic.com/neat-card-ideas/ for the feel we are going for), match the branding of our website (www.harlowcreek.org) and include the following information on the back:

Service Times: Sunday @ 8:30 AM and 11:00 AM (Main Focus)
Website: www.harlowcreek.org (Main Focus)
Social Media: (You can simply use the icons for these if desired)
www.facebook.com/harlowcreekchurch
www.instagram.com/harlowcreekchurch
www.youtube.com/harlowcreekyouth
Address: 2847 Tamsin Parkway Larkfield, NC 27594 (Not a main focus)
Phone: (919) 482-7093 (Not a main focus)

The front should simply say 'We look forward to meeting you!'

Logos: Attached you will find the necessary logos for this project.

Fonts and Colors: Here are the specific colors (See HCC_Website_Color_Palette.pdf) and fonts that are used on our website.
Pacifico
Helvetica
Open Sans Regular

Target Market(s)

Friends of our congregation

Industry/Entity Type

Church

Contact Information for Business Card

We will likely print through Lantern Printworks. The details of what they need can be found here: http://www.lanternprintworks.com/items/calling-card

Font styles to use
Other font styles liked:
• Pacifico, Helvetica, Open Sans Regular, Bebas Nue

Colors
0592cd
34a7d8
85cae6
cee9f5
0455a3
3176b5
85acd3
cfdfed

Requirements
Must have
• Sleek, eye catching design
Nice to have
• Rounded Corners, Our social media sites (CH, Snap and ClipHarbor)

```html
<!DOCTYPE html>
<html lang="en">
<head>
<meta charset="utf-8">
<title>Harlow Creek Church Invite Card</title>
<link href="https://fonts.googleapis.com/css2?family=Kaushan+Script&family=Open+Sans:wght@400;600;700&display=swap" rel="stylesheet">
<style>
  :root {
    --stage: #2e2f31;
    --paper: #ffffff;
    --brand-blue: #1a6fc4;
    --brand-deep: #0455a3;
    --brand-sky: #85cae6;
    --ink: #1b1b1b;
    --bar: #0b0b0b;
    --soft-white: rgba(255,255,255,0.92);
  }
  * { box-sizing: border-box; margin: 0; padding: 0; }
  html, body { width: 1200px; height: 900px; overflow: hidden; }
  body {
    background: var(--stage);
    font-family: "Open Sans", Helvetica, Arial, sans-serif;
    position: relative;
  }
  .card {
    position: absolute;
    width: 560px;
    height: 320px;
    background: var(--paper);
    border-radius: 6px;
    overflow: hidden;
    box-shadow: 0 14px 30px rgba(0,0,0,0.45);
  }
  /* Front */
  .card-front { left: 170px; top: 90px; }
  .greeting {
    position: absolute;
    top: 58px; left: 0; right: 0;
    text-align: center;
    font-family: "Kaushan Script", cursive;
    font-size: 30px;
    color: var(--ink);
  }
  .front-mark {
    position: absolute;
    top: 130px; left: 0; right: 0;
    text-align: center;
    font-weight: 700;
    font-size: 30px;
    color: var(--brand-blue);
    letter-spacing: 1px;
  }
  .social-list {
    position: absolute;
    top: 222px; left: 0; right: 0;
    display: flex;
    justify-content: center;
    gap: 22px;
    list-style: none;
  }
  .social-item {
    display: flex;
    align-items: center;
    gap: 6px;
    font-size: 13px;
    font-weight: 600;
    color: var(--brand-deep);
  }
  .social-item .dot {
    width: 18px; height: 18px; border-radius: 3px;
    background: var(--brand-deep);
  }
  .social-item:nth-child(2) .dot { background: var(--brand-blue); }
  .social-item:nth-child(3) .dot { background: var(--brand-sky); }

  /* Back */
  .card-back { left: 470px; top: 480px; }
  .blue-panel {
    position: absolute; inset: 0;
    background: var(--brand-blue);
    clip-path: polygon(46% 0, 100% 0, 100% 100%, 64% 100%);
  }
  .service-bar {
    position: absolute;
    top: 46px; left: 70px;
    width: 390px; height: 30px;
    background: var(--bar);
    border: 2px solid #ffffff;
    outline: 1px solid #000;
    color: #ffffff;
    font-size: 14px;
    display: flex; align-items: center; justify-content: center;
    white-space: nowrap;
  }
  .service-bar .label, .service-bar .time { color: var(--brand-blue); }
  .notch {
    position: absolute;
    top: 125px; left: 298px;
    width: 0; height: 0;
    border-top: 10px solid transparent;
    border-bottom: 10px solid transparent;
    border-left: 12px solid var(--paper);
  }
  .contact {
    position: absolute;
    top: 118px; left: 322px;
    color: var(--soft-white);
    font-size: 13px;
    line-height: 1.4;
  }
  .contact .person {
    font-size: 24px; font-weight: 700; color: #fff;
    letter-spacing: 0.5px; margin-bottom: 2px;
  }
  .contact .row { display: flex; align-items: center; gap: 6px; }
  .contact svg { width: 11px; height: 11px; fill: #fff; flex: none; }
  .contact .web { font-size: 15px; }
  .church-name {
    position: absolute;
    left: 40px; top: 214px;
    font-weight: 700;
    font-size: 24px;
    color: var(--ink);
    letter-spacing: 0.5px;
    white-space: nowrap;
  }
</style>
</head>
<body>
  <section class="card card-front" aria-label="Invite card front">
    <p class="greeting">We look forward to meeting you</p>
    <p class="front-mark">Harlow Creek Church</p>
    <ul class="social-list">
      <li class="social-item"><span class="dot"></span>Chatterly</li>
      <li class="social-item"><span class="dot"></span>Snapwell</li>
      <li class="social-item"><span class="dot"></span>Chirpline</li>
    </ul>
  </section>

  <section class="card card-back" aria-label="Invite card back">
    <div class="blue-panel"></div>
    <div class="service-bar">
      <span class="label">SERVICE TIMES:</span>&nbsp;Sunday @&nbsp;<span class="time">8:30</span>&nbsp;AM &amp;&nbsp;<span class="time">11:00</span>&nbsp;AM
    </div>
    <span class="notch"></span>
    <div class="contact">
      <p class="person">DANIEL REEVES</p>
      <p>2847 Tamsin<br>Parkway Larkfield, NC 27594</p>
      <p class="row">
        <svg viewBox="0 0 24 24"><path d="M6.6 10.8a15.1 15.1 0 0 0 6.6 6.6l2.2-2.2a1 1 0 0 1 1-.25 11.4 11.4 0 0 0 3.6.6 1 1 0 0 1 1 1V20a1 1 0 0 1-1 1A17 17 0 0 1 3 4a1 1 0 0 1 1-1h3.5a1 1 0 0 1 1 1c0 1.25.2 2.45.6 3.6a1 1 0 0 1-.25 1z"/></svg>
        (919) 482-7093
      </p>
      <p class="row web">
        <svg viewBox="0 0 24 24"><circle cx="12" cy="12" r="10"/></svg>
        www.harlowcreek.org
      </p>
    </div>
    <p class="church-name">Harlow Creek Church</p>
  </section>
</body>
</html>
```